Business card design needed

I would like a one sided black business card with the information provided above. Refer to my website www.brightvolleyracquets.com.au for an example of colors I have used for my site, would like to keep this consistent for my business cards also, I will upload my logo below.

I am a new small business that provides tennis customers with racquet re stringing, tennis strings and accessories.

Industry/Entity Type

Small Business

Contact Information for Business Card

Bright Volley Tennis

Owen Whitby
Managing Director

brightvolleyracquets@mailbox.example
www.brightvolleyracquets.com.au
0491 726 305

Racquet Restringing/Tennis Strings/Accessories

Requirements
Must have
• Must have my logo and card must be black

```html
<!DOCTYPE html>
<html lang="en">
<head>
<meta charset="utf-8">
<title>Bright Volley Tennis – Business Card</title>
<link rel="stylesheet" href="https://fonts.googleapis.com/css2?family=Questrial&display=swap">
<style>
  :root {
    --page-bg: #e7e4df;
    --card-black: #000000;
    --volley-green: #b6d334;
    --text-white: #f2f2f2;
    --band-text: #111111;
    --rule-grey: #8a8a8a;
  }
  * { margin: 0; padding: 0; box-sizing: border-box; }
  html, body {
    width: 1200px;
    height: 475px;
    overflow: hidden;
    background: var(--page-bg);
    font-family: "Questrial", "Century Gothic", sans-serif;
  }
  .canvas {
    position: relative;
    width: 1200px;
    height: 475px;
  }
  .card {
    position: absolute;
    top: 81px;
    width: 547px;
    height: 313px;
    background: var(--card-black);
    overflow: hidden;
  }
  .card--front { left: 39px; }
  .card--back { left: 602px; }

  .brand {
    position: absolute;
    left: 0;
    right: 0;
    display: flex;
    align-items: center;
    justify-content: center;
    gap: 14px;
  }
  .card--front .brand { top: 70px; }
  .card--back .brand { top: 116px; }
  .brand__dot {
    width: 44px;
    height: 44px;
    border-radius: 50%;
    background: var(--volley-green);
    flex: none;
  }
  .brand__name {
    color: var(--volley-green);
    font-size: 34px;
    letter-spacing: 1px;
    text-transform: uppercase;
    white-space: nowrap;
  }

  .holder {
    position: absolute;
    left: 61px;
    top: 200px;
    color: var(--volley-green);
  }
  .holder__name {
    font-size: 18px;
    letter-spacing: 1px;
    text-transform: uppercase;
  }
  .holder__role {
    font-size: 13.5px;
    margin-top: 3px;
  }
  .divider {
    position: absolute;
    left: 229px;
    top: 197px;
    width: 1px;
    height: 42px;
    background: var(--rule-grey);
  }
  .contact {
    position: absolute;
    left: 248px;
    top: 200px;
    color: var(--text-white);
    font-size: 14.5px;
    line-height: 20px;
    list-style: none;
  }
  .contact__label { margin-right: 4px; }

  .front-rule {
    position: absolute;
    left: 0;
    right: 0;
    top: 272px;
    height: 2px;
    background: var(--text-white);
  }
  .web-band {
    position: absolute;
    left: 0;
    right: 0;
    top: 278px;
    bottom: 0;
    background: var(--volley-green);
    display: flex;
    align-items: center;
    justify-content: center;
  }
  .web-band__url {
    color: var(--band-text);
    font-size: 13.5px;
    letter-spacing: 3px;
  }
  .back-url {
    position: absolute;
    left: 0;
    right: 0;
    top: 262px;
    text-align: center;
    color: var(--text-white);
    font-size: 13.5px;
    letter-spacing: 3px;
  }
</style>
</head>
<body>
<div class="canvas">
  <section class="card card--front" aria-label="Business card front">
    <div class="brand">
      <span class="brand__dot"></span>
      <span class="brand__name">Bright Volley Tennis</span>
    </div>

    <div class="holder">
      <p class="holder__name">Owen Whitby</p>
      <p class="holder__role">Managing Director</p>
    </div>
    <div class="divider"></div>
    <ul class="contact">
      <li><span class="contact__label">P :</span>0491 726 305</li>
      <li><span class="contact__label">E :</span>brightvolleyracquets@mailbox.example</li>
    </ul>

    <div class="front-rule"></div>
    <div class="web-band">
      <p class="web-band__url">www.brightvolleyracquets.com.au</p>
    </div>
  </section>

  <section class="card card--back" aria-label="Business card back">
    <div class="brand">
      <span class="brand__dot"></span>
      <span class="brand__name">Bright Volley Tennis</span>
    </div>
    <p class="back-url">www.brightvolleyracquets.com.au</p>
  </section>
</div>
</body>
</html>
```